Health Care Company with Logo Needs Business Cards designed

We are a luxury behavioral health company looking for business cards design we already have a logo and are looking for someone to design a sophisticated luxurious looking business card. Please note that Card design should be captivating just like the logo and also encompass the logo color

Industry/Entity Type

Healthcare

Contact Information for Business Card

Logo,company name, tagline, my name and title, contact details, and physical address

```html
<!DOCTYPE html>
<html lang="en">
<head>
<meta charset="utf-8">
<title>Corvan Behavioral Health – Business Cards</title>
<link rel="stylesheet" href="https://fonts.googleapis.com/css2?family=Roboto+Condensed:wght@700&family=Roboto:ital,wght@0,400;0,500;1,400&display=swap">
<style>
  :root {
    --backdrop: #2b2b2b;
    --card-white: #ececec;
    --card-dark: #252525;
    --brand-purple: #7b2f8c;
    --brand-blue: #1590d0;
    --text-grey: #3c3c3c;
  }
  * { margin: 0; padding: 0; box-sizing: border-box; }
  html, body { width: 1200px; height: 1138px; overflow: hidden; }
  body { background: var(--backdrop); position: relative; font-family: "Roboto", Arial, sans-serif; }

  .card {
    position: absolute;
    background: linear-gradient(160deg, #f2f2f2 0%, var(--card-white) 60%, #dedede 100%);
    border-radius: 16px;
    overflow: hidden;
    box-shadow: 0 6px 14px rgba(0,0,0,0.45);
  }
  .card-front { left: 274px; top: 186px; width: 623px; height: 376px; }
  .card-back  { left: 276px; top: 608px; width: 618px; height: 374px; }

  .front-name {
    position: absolute; left: 0; right: 0; top: 148px;
    text-align: center;
    font-family: "Roboto Condensed", "Arial Narrow", sans-serif;
    font-weight: 700; font-size: 46px; color: var(--brand-purple);
    letter-spacing: 0.2px;
  }
  .front-tagline {
    position: absolute; left: 0; right: 0; top: 203px;
    text-align: center;
    font-family: "Roboto Condensed", "Arial Narrow", sans-serif;
    font-weight: 700; font-size: 13.5px; color: var(--brand-blue);
    letter-spacing: 3.6px;
  }

  .back-shape { position: absolute; inset: 0; }

  .person-name {
    position: absolute; left: 58px; top: 70px;
    font-weight: 500; font-size: 23px; color: var(--brand-purple);
  }
  .person-title {
    position: absolute; left: 58px; top: 99px;
    font-style: italic; font-size: 14.5px; color: var(--text-grey);
  }
  .address {
    position: absolute; left: 58px; top: 194px;
    font-size: 14.5px; line-height: 21.5px; color: var(--text-grey);
  }
  .contact-list { position: absolute; left: 58px; top: 240px; list-style: none; }
  .contact-list li {
    display: flex; align-items: center; height: 22px;
    font-size: 14.5px; color: var(--text-grey);
  }
  .contact-list svg { width: 15px; height: 13px; margin-right: 17px; }

  .brand-mark {
    position: absolute; left: 388px; top: 136px;
    width: 104px; height: 104px; border-radius: 50%;
    background: var(--brand-purple);
  }
  .brand-vertical {
    position: absolute; left: 512px; top: 186px;
    width: 300px; height: 60px;
    transform-origin: 0 0;
    transform: translate(0, 0) rotate(-90deg) translate(-50%, 0);
  }
  .brand-vertical-name {
    display: block; text-align: center;
    font-family: "Roboto Condensed", "Arial Narrow", sans-serif;
    font-weight: 700; font-size: 33px; line-height: 36px; color: var(--brand-purple);
  }
  .brand-vertical-tagline {
    display: block; text-align: center;
    font-family: "Roboto Condensed", "Arial Narrow", sans-serif;
    font-weight: 700; font-size: 9.5px; line-height: 14px; color: var(--brand-blue);
    letter-spacing: 2.2px; white-space: nowrap;
  }
</style>
</head>
<body>

  <section class="card card-front">
    <h1 class="front-name">Corvan Behavioral Health</h1>
    <p class="front-tagline">DEDICATED TO HOPE, HEALING AND RECOVERY</p>
  </section>

  <section class="card card-back">
    <svg class="back-shape" width="618" height="374" viewBox="0 0 618 374">
      <defs>
        <linearGradient id="edgeGradient" x1="0" y1="0" x2="0" y2="1">
          <stop offset="0" stop-color="#1590d0"/>
          <stop offset="0.55" stop-color="#3a5fb0"/>
          <stop offset="1" stop-color="#7b2f8c"/>
        </linearGradient>
      </defs>
      <path d="M386,0 Q238,187 396,374 L384,374 Q236,187 380,0 Z" fill="url(#edgeGradient)"/>
      <path d="M388,0 Q248,187 392,374 L618,374 L618,0 Z" fill="var(--card-dark)"/>
    </svg>

    <h2 class="person-name">DANIEL REEVE</h2>
    <p class="person-title">Managing Director</p>
    <p class="address">123, Anywhere ST, Any City,<br>Any Town, US 123456</p>

    <ul class="contact-list">
      <li>
        <svg viewBox="0 0 15 13"><path d="M1 4 Q7.5 -1 14 4 L12 5.5 L10.5 4 L4.5 4 L3 5.5 Z M3.5 6 L11.5 6 L13 12 L2 12 Z" fill="var(--brand-purple)"/></svg>
        000-111-0000
      </li>
      <li>
        <svg viewBox="0 0 15 13"><rect x="0.5" y="1.5" width="14" height="10" fill="var(--brand-purple)"/><path d="M0.5 1.5 L7.5 7 L14.5 1.5 M0.5 11.5 L5.5 6 M14.5 11.5 L9.5 6" stroke="#fff" stroke-width="1" fill="none"/></svg>
        daniel@corvanbehavioral.com
      </li>
      <li>
        <svg viewBox="0 0 15 13"><circle cx="7.5" cy="6.5" r="6" fill="var(--brand-blue)"/><path d="M1.5 6.5 H13.5 M7.5 0.5 V12.5 M2.5 3.5 H12.5 M2.5 9.5 H12.5" stroke="#fff" stroke-width="0.8"/><ellipse cx="7.5" cy="6.5" rx="2.6" ry="6" stroke="#fff" stroke-width="0.8" fill="none"/></svg>
        www.corvanbehavioral.com
      </li>
    </ul>

    <div class="brand-mark" aria-hidden="true"></div>
    <div class="brand-vertical">
      <span class="brand-vertical-name">Corvan Behavioral Health</span>
      <span class="brand-vertical-tagline">DEDICATED TO HOPE, HEALING AND RECOVERY</span>
    </div>
  </section>

</body>
</html>
```